Marlowe Group needs a business card

I would like the card to be simple but modern and elegant.
I like black and white.
or black and gold.
we are a private finance lender and also are involved in property and property developments.

please look at the business card photos i provided i would like M.G only one one side and all the other details on the other side use fonts that tie in with my theme.

Industry/Entity Type

Finance

Contact Information for Business Card

Marlowe Group (M.G) Daniel Marlowe M: 0413586207 E: danmarl@inboxmail.test

Font styles to use
Other font styles liked:
• Use fonts that would reflect our business

Colors
000000
ffffff

Requirements
Must have
• one side of details
• other side has either M.G or Marlowe Group like in the photos provided

```html
<!DOCTYPE html>
<html lang="en">
<head>
<meta charset="utf-8">
<title>Marlowe Group – Business Card</title>
<link href="https://fonts.googleapis.com/css2?family=Open+Sans:wght@400;600;700;800&display=swap" rel="stylesheet">
<style>
  :root {
    --backdrop: #e9e6e1;
    --card-white: #ffffff;
    --ink: #000000;
    --ink-soft: #4a4a4a;
    --band-grey: #6e6e6e;
    --gold: #c9a640;
    --shadow: rgba(0, 0, 0, 0.28);
  }
  * { margin: 0; padding: 0; box-sizing: border-box; }
  html, body {
    width: 1200px;
    height: 987px;
    overflow: hidden;
    background: var(--backdrop);
    font-family: "Open Sans", Arial, sans-serif;
  }
  .canvas {
    position: relative;
    width: 1200px;
    height: 987px;
  }
  .card {
    position: absolute;
    left: 292px;
    width: 616px;
    height: 352px;
    box-shadow: 0 2px 6px var(--shadow);
    overflow: hidden;
  }
  .card--front { top: 130px; background: var(--card-white); }
  .card--back  { top: 505px; background: var(--ink); }

  .edge-band {
    position: absolute;
    left: 0;
    top: 0;
    width: 21px;
    height: 352px;
  }
  .wordmark {
    position: absolute;
    left: 56px;
    top: 42px;
    display: flex;
    align-items: center;
    gap: 10px;
    font-weight: 800;
    font-size: 28px;
    letter-spacing: 1px;
    color: var(--ink);
  }
  .wordmark__mark {
    width: 12px;
    height: 12px;
    background: var(--ink);
  }
  .contact {
    position: absolute;
    left: 376px;
    top: 216px;
  }
  .contact__name {
    font-weight: 600;
    font-size: 23px;
    color: var(--ink);
    margin-bottom: 14px;
  }
  .contact__line {
    font-size: 16px;
    line-height: 23.5px;
    color: var(--ink-soft);
  }
  .contact__label {
    font-weight: 700;
    color: var(--ink);
  }
  .monogram {
    position: absolute;
    inset: 0;
    display: flex;
    align-items: center;
    justify-content: center;
    font-weight: 800;
    font-size: 92px;
    letter-spacing: 4px;
    color: var(--gold);
  }
</style>
</head>
<body>
  <main class="canvas">
    <section class="card card--front">
      <svg class="edge-band" viewBox="0 0 21 352" aria-hidden="true">
        <polygon points="0,0 21,0 21,120 0,140" fill="var(--band-grey)"/>
        <polygon points="0,140 21,120 21,352 0,352" fill="var(--ink)"/>
        <line x1="0" y1="141" x2="21" y2="121" stroke="#ffffff" stroke-width="1.5"/>
      </svg>
      <div class="wordmark">
        <span class="wordmark__text">MARLOWE GROUP</span>
        <span class="wordmark__mark"></span>
      </div>
      <div class="contact">
        <p class="contact__name">Daniel Marlowe</p>
        <p class="contact__line"><span class="contact__label">Cell :</span> 0413586207</p>
        <p class="contact__line">danmarl@inboxmail.test</p>
        <p class="contact__line">www.marlowegroup.test</p>
      </div>
    </section>

    <section class="card card--back">
      <p class="monogram">M.G</p>
    </section>
  </main>
</body>
</html>
```